Pain cream backed by Pro-Athletes "Glacier Ember"

Looking to revamp the label brand.
It's an all-natural pain gel. It heats then cools. Looking for a very sharp look that gets the point of the product use across.
Eveyrthing about the original label can be changed except for the text. It still needs to have the same information but can be any color, font whatever.,
I'll need pdf's and ai files of the design.
Label Size die line is attached.
Original Label is attached.

```html
<!DOCTYPE html>
<html lang="en">
<head>
<meta charset="utf-8">
<title>Glacier Ember – Pain Gel Label</title>
<link rel="stylesheet" href="https://fonts.googleapis.com/css2?family=Exo+2:ital,wght@0,800;1,700&family=Montserrat:wght@400&display=swap">
<style>
  :root {
    --backdrop: #dcdcdc;
    --navy-deep: #10113a;
    --navy-mid: #2a2a6a;
    --navy-glow: #55578f;
    --ember-orange: #f6a12a;
    --ember-red: #d8231a;
    --ice-blue: #1a73c9;
    --ice-cyan: #3fd3f5;
    --text-light: #ffffff;
    --text-soft: #c9cbe6;
  }
  * { margin: 0; padding: 0; box-sizing: border-box; }
  html, body {
    width: 1200px;
    height: 884px;
    overflow: hidden;
    background: var(--backdrop);
  }
  .canvas {
    position: relative;
    width: 1200px;
    height: 884px;
    display: flex;
    align-items: center;
    justify-content: center;
  }
  .label {
    position: relative;
    width: 520px;
    height: 760px;
    overflow: hidden;
    background:
      radial-gradient(ellipse 60% 45% at 45% 52%, var(--navy-glow) 0%, var(--navy-mid) 45%, var(--navy-deep) 100%);
    box-shadow: 0 10px 30px rgba(0, 0, 0, 0.18);
  }
  .brand {
    position: absolute;
    top: 130px;
    left: 0;
    right: 0;
    display: flex;
    flex-direction: column;
    align-items: center;
    gap: 34px;
  }
  .brand-mark {
    width: 74px;
    height: 74px;
    border-radius: 50%;
    background: var(--ember-orange);
  }
  .brand-name {
    font-family: "Exo 2", sans-serif;
    font-weight: 800;
    font-size: 66px;
    line-height: 0.95;
    letter-spacing: 1px;
    text-align: center;
    color: var(--ice-cyan);
    text-transform: uppercase;
  }
  .tagline {
    position: absolute;
    top: 420px;
    left: 0;
    right: 0;
    text-align: center;
    font-family: "Exo 2", sans-serif;
    font-style: italic;
    font-weight: 700;
    font-size: 30px;
    letter-spacing: 0.5px;
    color: var(--text-light);
    text-transform: uppercase;
  }
  .band-area {
    position: absolute;
    left: 0;
    right: 0;
    top: 500px;
    height: 170px;
    background: linear-gradient(160deg,
      rgba(246, 161, 42, 0.55) 0%,
      rgba(63, 211, 245, 0.45) 50%,
      rgba(216, 35, 26, 0.5) 100%);
  }
  .volume {
    position: absolute;
    left: 56px;
    bottom: 48px;
    font-family: "Montserrat", sans-serif;
    font-weight: 400;
    font-size: 15px;
    color: var(--text-soft);
  }
</style>
</head>
<body>
  <main class="canvas">
    <section class="label">
      <div class="brand">
        <span class="brand-mark"></span>
        <h1 class="brand-name">Glacier<br>Ember</h1>
      </div>

      <p class="tagline">Gets you back up</p>

      <div class="band-area" role="img" aria-label="Decorative warm-to-cool stripe band across the lower label"></div>

      <p class="volume">100 ML (3.2oz)</p>
    </section>
  </main>
</body>
</html>
```